Cocktail-Making Assistant App re-design

Ok boys and girls, here's the deal:
I have an android app which is almost complete, but needs a design overhaul.

The app is a standard cocktail-making assistant: gives you a list of cocktails and the ability to see which cocktail you can make out of those ingredients (drinks, fruit, etc) you have at home.

I've attached some general app flow, as well as detailed requirements/explanation presentation. Most of those things are just FYI, so that you know what it's about.

3 screens are the most important (main screen, cocktail view screen, ingredient view screen), meaning I will pick the design mostly based on ideas for those 3 things, with the fourth being a rather simple list (given on attached flow, third tier)
Some other screens are derived from that, with some minor changes on it, but you shouldn't care about that.

There are lots of other, non-explained things which I said nothing about only because they are (from design point of view) completely the same and would only make it seem more complicated.

I don't want to influence the colour scheme, but the app will be released under RedFig developer name (having a light colured red fig as a logo) so I suppose some brownish design, for example, will not really fit nicely. If you, however, have a killer which you are confident will prove me wrong, I'm looking forward to seeing it!

It should be a serious, elegant look (as opposed to cartoonish, but we are not aiming for a business look at all!), not cluttered with details, no clubbing themes, glitter and so on.

Test apk file available on request (Android 2.3+).

Edit: payment is now guaranteed
Also please note that currently, the favorite, "heart" button has a motion effect:
on click it flies out of the screen to the left (white heart) and comes back to the screen as a red heart. Take that into consideration, if it means anything to you.

Target Market(s)

Whoever you imagine would enjoy drinking cocktails

Industry/Entity Type

Business

Requirements
Must have
• Everything is said in the provided documentation - images say more than I could possibly write here.
Nice to have
• As said, most of the icons are a nice-to-have. Only those which are critically linked to the rest of the design must be provided. More details in the docs.
Should not have
• No cartoon look, No zillion colours

```html
<!DOCTYPE html>
<html lang="en">
<head>
<meta charset="utf-8">
<title>RedFig – Main Menu</title>
<link rel="stylesheet" href="https://fonts.googleapis.com/css2?family=Dancing+Script:wght@500&family=Marcellus&family=Open+Sans:wght@400&display=swap">
<style>
  :root {
    --bg-top: #17176a;
    --bg-mid: #1d1b4a;
    --bg-bottom: #231f20;
    --wheel-line: #e6e6ef;
    --label: #e2532d;
    --title: #a9c6c9;
    --hub-top: #7b82b6;
    --hub-bottom: #1c2263;
    --icon-blue: #2a8fd8;
    --heart: #c8261f;
    --cart: #e8e8e8;
    --ribbon: #3fb6de;
    --footer: #f2f2f2;
  }
  * { margin: 0; padding: 0; box-sizing: border-box; }
  html, body { width: 982px; height: 1200px; overflow: hidden; }
  body { background: var(--bg-bottom); }
  .screen {
    position: relative;
    width: 982px; height: 1200px;
    background: linear-gradient(160deg, var(--bg-top) 0%, var(--bg-mid) 45%, var(--bg-bottom) 80%);
    overflow: hidden;
  }
  .app-title {
    position: absolute; left: 48px; top: 40px;
    font-family: "Marcellus", serif;
    font-size: 68px; color: var(--title);
    letter-spacing: 1px;
  }
  .wheel { position: absolute; left: 0; top: 0; }
  .menu-label {
    position: absolute;
    font-family: "Dancing Script", cursive;
    font-size: 44px; font-weight: 500;
    color: var(--label);
    white-space: nowrap;
    line-height: 1;
  }
  .placeholder { position: absolute; border-radius: 6px; }
  .bottles { left: 518px; top: 281px; width: 180px; height: 134px;
    background: linear-gradient(90deg, #e9d23a, #c8203a 30%, #c9d83c 60%, #e8b52a); }
  .shaker { left: 140px; top: 532px; width: 67px; height: 172px; border-radius: 14px 14px 8px 8px;
    background: linear-gradient(90deg, #6e6e6e, #f4f4f4 40%, #9a9a9a 70%, #e0e0e0); }
  .glasses { left: 682px; top: 573px; width: 169px; height: 60px;
    background: linear-gradient(90deg, #b43a1e, #d9d3a0 30%, #3f8a3a 55%, #cfcfbf 75%, #c32b2b); }
  .points {
    position: absolute; left: 380px; top: 492px; width: 200px;
    text-align: center;
    font-family: "Open Sans", sans-serif; font-size: 22px;
    color: var(--label);
  }
  .brand-footer {
    position: absolute; left: 0; right: 0; top: 1142px;
    text-align: center;
    font-family: "Marcellus", serif; font-size: 27px;
    color: var(--footer);
  }
</style>
</head>
<body>
<main class="screen">
  <h1 class="app-title">RedFig</h1>

  <svg class="wheel" width="982" height="1200" viewBox="0 0 982 1200" aria-hidden="true">
    <g stroke="var(--wheel-line)" stroke-width="1.3" fill="none">
      <circle cx="480" cy="586" r="437"/>
      <line x1="480" y1="149" x2="480" y2="460"/>
      <line x1="480" y1="712" x2="480" y2="1023"/>
      <line x1="858" y1="367" x2="589" y2="523"/>
      <line x1="102" y1="367" x2="371" y2="523"/>
      <line x1="858" y1="805" x2="589" y2="649"/>
      <line x1="102" y1="805" x2="371" y2="649"/>
    </g>

    <!-- hub -->
    <defs>
      <clipPath id="hub-clip"><circle cx="480" cy="586" r="126"/></clipPath>
    </defs>
    <g clip-path="url(#hub-clip)">
      <rect x="354" y="460" width="252" height="252" fill="var(--hub-top)"/>
      <path d="M354 590 C 420 580, 470 598, 530 590 S 590 584, 606 588 L606 712 L354 712 Z" fill="var(--hub-bottom)"/>
    </g>
    <circle cx="480" cy="586" r="126" fill="none" stroke="var(--wheel-line)" stroke-width="1.3"/>

    <!-- home button -->
    <circle cx="480" cy="565" r="38" fill="var(--icon-blue)" stroke="#cfe6f7" stroke-width="3"/>
    <path d="M459 568 L480 549 L501 568 M464 565 V583 H496 V565" fill="none" stroke="#fff" stroke-width="5" stroke-linejoin="round"/>

    <!-- settings gears -->
    <g fill="none" stroke="#9aa0ad" stroke-width="5" stroke-dasharray="3 3">
      <circle cx="472" cy="650" r="9"/>
      <circle cx="490" cy="664" r="7"/>
    </g>
    <circle cx="472" cy="650" r="4" fill="#9aa0ad"/>
    <circle cx="490" cy="664" r="3" fill="#9aa0ad"/>

    <!-- favorites heart -->
    <path d="M355 415 C 330 390, 289 360, 289 330 C 289 305, 310 292, 330 296 C 345 299, 352 308, 355 316 C 360 306, 372 295, 392 295 C 412 296, 420 314, 418 332 C 414 365, 380 392, 355 415 Z" fill="var(--heart)"/>
    <circle cx="338" cy="378" r="21" fill="var(--icon-blue)" stroke="#e0f0fb" stroke-width="2"/>
    <path d="M338 366 V390 M326 378 H350" stroke="#fff" stroke-width="6"/>

    <!-- shopping cart -->
    <g fill="none" stroke="var(--cart)" stroke-width="7" stroke-linejoin="round">
      <path d="M300 870 H385 L378 912 H318 Z"/>
      <path d="M385 870 L392 856 H409"/>
      <line x1="306" y1="884" x2="381" y2="884"/>
      <line x1="311" y1="898" x2="379" y2="898"/>
    </g>
    <circle cx="326" cy="923" r="5" fill="var(--cart)"/>
    <circle cx="370" cy="923" r="5" fill="var(--cart)"/>

    <!-- featured rosette -->
    <path d="M604 900 L588 975 L603 962 L614 982 L622 905 Z" fill="var(--ribbon)"/>
    <path d="M632 900 L650 975 L634 962 L624 982 L614 905 Z" fill="#2a97bd"/>
    <circle cx="619" cy="877" r="36" fill="var(--ribbon)" stroke="#8fd9f0" stroke-width="4" stroke-dasharray="6 3"/>
    <circle cx="619" cy="877" r="25" fill="#5cc6e8"/>
  </svg>

  <span class="menu-label" style="left:262px; top:210px;">favorites</span>
  <span class="menu-label" style="left:529px; top:202px;">my bar</span>
  <span class="menu-label" style="left:96px; top:463px;">shaker</span>
  <span class="menu-label" style="left:671px; top:474px;">cocktails</span>
  <span class="menu-label" style="left:218px; top:774px;">shopping list</span>
  <span class="menu-label" style="left:518px; top:772px;">featured</span>

  <div class="placeholder bottles" role="img" aria-label="Photo of four liqueur bottles in yellow, red and green"></div>
  <div class="placeholder shaker" role="img" aria-label="Photo of a chrome cocktail shaker"></div>
  <div class="placeholder glasses" role="img" aria-label="Photo of a row of five colourful cocktail glasses"></div>

  <div class="points">Points :100</div>

  <footer class="brand-footer">redfig</footer>
</main>
</body>
</html>
```